Indy Film Production Company/Studio

We need a business card designed from an existing logo. We are a digital studio/production company that caters to creating genre entertainment, like Action, Horror, and martial arts. The card along with the logo will be used to Brand the company from letter heads to banners. The design will also be used for postcards and Brochures. It should be professional and masculine.
Updates

Thank you to all the designers who have participated. I'm narrowing down who it will be. Thank you again.

Target Market(s)

Investors, Networks, Producers, and actors

Industry/Entity Type

Film Production

Contact Information for Business Card

Teodoro Valbuena
Producer/Writer/Director
www.kestrelpicturehouse.example

Requirements
Must have
• Website address, Facebook icon and Twitter icon possibly in the back of the card.
Nice to have
• Logline of Company: Follow The Action.

```html
<!DOCTYPE html>
<html lang="en">
<head>
<meta charset="utf-8">
<title>Kestrel Picture House – Business Card</title>
<link href="https://fonts.googleapis.com/css2?family=Roboto+Condensed:wght@500;700&family=Source+Sans+3:wght@400;600&display=swap" rel="stylesheet">
<style>
  :root {
    --stage: #3b3b3b;
    --brand-red: #e31b23;
    --paper: #f7f7f7;
    --ink-light: #ffffff;
    --divider: rgba(255,255,255,0.75);
  }
  * { margin: 0; padding: 0; box-sizing: border-box; }
  html, body { width: 1200px; height: 750px; overflow: hidden; }
  body { background: var(--stage); position: relative; }

  .card {
    position: absolute;
    left: 371px;
    width: 462px;
    height: 263px;
  }
  .card--front { top: 81px; background: var(--brand-red); color: var(--ink-light); }
  .card--back { top: 382px; background: var(--paper); }

  .corner {
    position: absolute;
    width: 22px;
    height: 22px;
    border-color: var(--ink-light);
    border-style: solid;
    border-width: 0;
  }
  .card--back .corner { border-color: var(--brand-red); }
  .corner--tl { top: 9px; left: 10px; border-top-width: 2px; border-left-width: 2px; }
  .corner--tr { top: 9px; right: 10px; border-top-width: 2px; border-right-width: 2px; }
  .corner--bl { bottom: 9px; left: 10px; border-bottom-width: 2px; border-left-width: 2px; }
  .corner--br { bottom: 9px; right: 10px; border-bottom-width: 2px; border-right-width: 2px; }

  .contact {
    position: absolute;
    top: 80px;
    left: 50%;
    width: 190px;
    transform: translateX(-45%);
    text-align: center;
  }
  .contact__name {
    font-family: "Roboto Condensed", sans-serif;
    font-weight: 500;
    font-size: 17px;
    line-height: 20px;
    text-transform: uppercase;
  }
  .contact__role {
    font-family: "Roboto Condensed", sans-serif;
    font-weight: 500;
    font-size: 12.5px;
    line-height: 16px;
    text-transform: uppercase;
    white-space: nowrap;
  }
  .contact__details {
    margin-top: 6px;
    padding: 5px 0 4px;
    border-top: 1px dotted var(--divider);
    border-bottom: 1px dotted var(--divider);
    font-family: "Source Sans 3", sans-serif;
    font-size: 12.5px;
    line-height: 17.5px;
    white-space: nowrap;
  }
  .contact__details .label { font-weight: 600; }
  .social {
    display: flex;
    justify-content: center;
    gap: 2px;
    margin-top: 9px;
  }
  .social__square { width: 15px; height: 15px; background: var(--ink-light); }

  .wordmark {
    position: absolute;
    top: 50%;
    left: 50%;
    transform: translate(-50%, -50%);
    font-family: "Roboto Condensed", sans-serif;
    font-weight: 700;
    font-size: 30px;
    line-height: 34px;
    letter-spacing: 1px;
    text-transform: uppercase;
    color: var(--brand-red);
    text-align: center;
    white-space: nowrap;
  }
</style>
</head>
<body>
  <section class="card card--front" aria-label="Card front">
    <span class="corner corner--tl"></span>
    <span class="corner corner--tr"></span>
    <span class="corner corner--bl"></span>
    <span class="corner corner--br"></span>
    <div class="contact">
      <h1 class="contact__name">Teodoro Valbuena</h1>
      <p class="contact__role">Producer/Writer/Director</p>
      <div class="contact__details">
        <p><span class="label">P :</span> 555 014 2730</p>
        <p>mail@kestrelpicturehouse.example</p>
        <p>www.kestrelpicturehouse.example</p>
      </div>
      <div class="social" aria-label="Social links">
        <span class="social__square"></span>
        <span class="social__square"></span>
      </div>
    </div>
  </section>

  <section class="card card--back" aria-label="Card back">
    <span class="corner corner--tl"></span>
    <span class="corner corner--tr"></span>
    <span class="corner corner--bl"></span>
    <span class="corner corner--br"></span>
    <p class="wordmark">Kestrel Picture House</p>
  </section>
</body>
</html>
```